A Modern & Sleek "Coming Soon" Page for an A.I Recruiting App

For the “Coming Soon” website, a simple background with no people in it. I've attached an A.I image of what the page should generally look like.

- A single mobile phone as the main focus where the user actually clicks on the, “notify me” button (after entering their email address).
- In the background where the pillars/columns are seen in the example, should be subtle pad locks that are in their opened position with a key inside the lock. I've attached images to try to illustrate this idea, but they are far away in style from what I'm looking for.

SLOGAN: Unlocking the power of meaningful connections
LOGO/TITLE: Should be the name as shown in image with only the name "KelvoLink" on it
COLORS: Purplish/blue hues. Should not be too feminine
NOTE: The user should only click once when signing up/entering their email.

Product: A recruiting platform that matches employers/employees with A.I. and prioritizing cultural fit/values system before skills. The industry we are tackling first is the caregiving industry (nannies, tutors, elderly). All users will be background screened and that info lives on the blockchain. All users will have the option to review and be reviewed/rated.

```html
<!DOCTYPE html>
<html lang="en">
<head>
<meta charset="utf-8">
<title>KelvoLink — Coming Soon</title>
<link href="https://fonts.googleapis.com/css2?family=Source+Sans+3:wght@300;400;600;700&display=swap" rel="stylesheet">
<style>
  :root {
    --bg-deep: #12020d;
    --bg-mid: #3a0a2c;
    --lock-light: rgba(205, 150, 190, 0.55);
    --lock-mid: rgba(150, 60, 125, 0.55);
    --screen-top: #b22a8e;
    --screen-bottom: #6a0a4c;
    --frame: #1b1b1f;
    --frame-edge: #55555c;
    --field: rgba(255, 255, 255, 0.14);
    --text: #ffffff;
    --text-soft: #f3e6ef;
  }
  * { margin: 0; padding: 0; box-sizing: border-box; }
  html, body { width: 1200px; height: 729px; overflow: hidden; background: var(--bg-deep); }
  body { font-family: "Source Sans 3", sans-serif; color: var(--text); }

  .page { position: relative; width: 1200px; height: 729px; overflow: hidden; }

  .hero-backdrop {
    position: absolute; inset: 0;
    background:
      radial-gradient(ellipse 700px 260px at 900px 80px, rgba(120, 30, 95, 0.45), transparent 75%),
      linear-gradient(180deg, var(--bg-mid) 0%, var(--bg-deep) 45%, #2a0620 100%);
  }

  .padlock-visual {
    position: absolute; left: 446px; top: 146px; width: 702px; height: 437px;
    border-radius: 45% 45% 40% 40%;
    background:
      radial-gradient(ellipse 130px 170px at 120px 150px, var(--lock-light), transparent 72%),
      radial-gradient(ellipse 300px 200px at 430px 260px, var(--lock-mid), transparent 75%),
      radial-gradient(ellipse 90px 90px at 600px 360px, var(--lock-light), transparent 75%);
  }

  .brand {
    position: absolute; left: 114px; top: 58px;
    font-size: 48px; font-weight: 300; letter-spacing: 10px; text-transform: uppercase;
    line-height: 1;
  }

  .menu-toggle { position: absolute; left: 1028px; top: 58px; }

  .phone {
    position: absolute; left: 112px; top: 159px; width: 231px; height: 482px;
    background: var(--frame); border: 1.5px solid var(--frame-edge); border-radius: 34px;
    padding: 7px;
  }
  .phone-screen {
    position: relative; width: 100%; height: 100%; border-radius: 28px; overflow: hidden;
    background: linear-gradient(180deg, var(--screen-top) 0%, #8e1770 55%, var(--screen-bottom) 100%);
    text-align: center;
  }
  .phone-notch {
    position: absolute; left: 50%; top: 0; transform: translateX(-50%);
    width: 88px; height: 22px; background: var(--frame); border-radius: 0 0 12px 12px;
  }
  .phone-camera {
    position: absolute; left: 10px; top: 5px; width: 9px; height: 9px; border-radius: 50%;
    background: #f4f4f4;
  }
  .phone-brand {
    position: absolute; top: 78px; left: 0; right: 0;
    font-size: 27px; font-weight: 300; letter-spacing: 3.5px; text-transform: uppercase;
  }
  .phone-slogan {
    position: absolute; top: 211px; left: 0; right: 0;
    font-size: 14.5px; line-height: 19px; color: var(--text-soft);
  }
  .email-field {
    position: absolute; top: 298px; left: 28px; width: 158px; height: 28px;
    border: 1px solid rgba(255, 255, 255, 0.6); border-radius: 14px;
    background: var(--field); color: var(--text);
    font: 400 11.5px "Source Sans 3", sans-serif; text-align: center; outline: none;
  }
  .email-field::placeholder { color: var(--text-soft); }
  .phone-button {
    position: absolute; top: 351px; left: 53px; width: 111px; height: 30px;
    border: 1.5px solid var(--text); border-radius: 15px;
    font-size: 12px; font-weight: 600; line-height: 27px;
  }
  .phone-note {
    position: absolute; top: 395px; left: 0; right: 0;
    font-size: 10.5px; line-height: 13px; color: var(--text-soft);
  }
  .phone-home-bar {
    position: absolute; top: 446px; left: 72px; width: 73px; height: 1px; background: var(--text-soft);
  }

  .hero-copy { position: absolute; left: 596px; top: 258px; }
  .hero-title { font-size: 70px; font-weight: 700; line-height: 1; letter-spacing: -0.5px; }
  .hero-slogan {
    margin-top: 18px; margin-left: 10px; width: 520px;
    font-size: 31px; font-weight: 400; line-height: 43px;
  }
  .signup-button {
    display: block; margin-top: 30px; margin-left: 10px; width: 154px; height: 42px;
    border: 1.5px solid var(--text); border-radius: 21px;
    text-align: center; font-size: 17px; font-weight: 700; line-height: 39px;
  }
</style>
</head>
<body>
<main class="page">
  <div class="hero-backdrop"></div>
  <div class="padlock-visual" role="img" aria-label="Open circuit-patterned padlock with a key in its lock, surrounded by floating binary digits"></div>

  <header>
    <div class="brand">KelvoLink</div>
    <svg class="menu-toggle" width="60" height="42" viewBox="0 0 60 42" aria-label="Menu">
      <line x1="20" y1="4" x2="57" y2="4" stroke="#fff" stroke-width="5" stroke-linecap="round"/>
      <line x1="3" y1="21" x2="57" y2="21" stroke="#fff" stroke-width="5" stroke-linecap="round"/>
      <line x1="12" y1="38" x2="57" y2="38" stroke="#fff" stroke-width="5" stroke-linecap="round"/>
    </svg>
  </header>

  <div class="phone">
    <div class="phone-screen">
      <div class="phone-notch"><span class="phone-camera"></span></div>
      <div class="phone-brand">KelvoLink</div>
      <p class="phone-slogan">Unlocking the power<br>of meaningful connections</p>
      <input class="email-field" type="email" placeholder="Enter your email" aria-label="Email address">
      <div class="phone-button">Notify Me</div>
      <p class="phone-note">Excepteur sint occaecat<br>sunt in culpa qui est laborum.</p>
      <div class="phone-home-bar"></div>
    </div>
  </div>

  <section class="hero-copy">
    <h1 class="hero-title">KelvoLink</h1>
    <p class="hero-slogan">Unlocking the power of meaningful connections</p>
    <span class="signup-button">Sign Up</span>
  </section>
</main>
</body>
</html>
```